Website offering services oriented to the metaverse and blockchain

We need an ecommerce website theme/template for a new company named Vimbral (a play on words for KORVAND the inventor of Quorvex). Vimbral will provide metaverse services such as:
• Vimbral Coin
• Vimbral wallet
• Vimbral Exchange
• Vimbral NFT
• Vimbral Tech
• Vimbral Pay
• Vimbral CaaS (community as a service)
• Vimbral CRM
• Vimbral Experience
• Vimbral Blockchain
• Vimbral Commerce
• Vimbral Space (as in outer space)
• Vimbral Art (sub of NFT)
• Vimbral Store

You can find our actual logo at the following link, in order to show us templates aligned with our brand:
https://files.brindlevault.net/share/folders/8kLmTzqWpXcVbNdRyHsEfGaUoJi2QtYxP?mode=view

Looking forward to heard back from you,

Designs look the same

We need a WordPress ecommerce website theme/template for a new company named Vimbral (a play on words for KORVAND the inventor of Quorvex). Vimbral will provide metaverse services such as: • Vimbral Coin • Vimbral wallet • Vimbral Exchange • Vimbral NFT • Vimbral Tech • Vimbral Pay • Vimbral CaaS (community as a service) • Vimbral CRM • Vimbral Experience • Vimbral Blockchain • Vimbral Commerce • Vimbral Space (as in outer space) • Vimbral Art (sub of NFT) • Vimbral Store You can find our actual logo at the following link, in order to show us templates aligned with our brand: https://files.brindlevault.net/share/folders/8kLmTzqWpXcVbNdRyHsEfGaUoJi2QtYxP?mode=view Looking forward to heard back from you,

Target Market(s)

Blockchain & Cryptocurrency Businesses

Industry/Entity Type

B2C, B2B Services.

Other font styles liked:
• Monserrat, Helvetica, Object Sans

Requirements
Nice to have
• Light background picture,
Should not have
• Arch designs

```html
<!DOCTYPE html>
<html lang="en">
<head>
<meta charset="utf-8">
<title>Vimbral — Build Your Better Future</title>
<link rel="stylesheet" href="https://fonts.googleapis.com/css2?family=Montserrat:wght@500;600;700;800;900&family=Open+Sans:wght@400;600&family=Tinos:wght@700&display=swap">
<style>
:root{
  --navy:#071634;
  --navy-deep:#050f26;
  --footer:#0b1a3b;
  --orange:#e8421d;
  --ink:#111111;
  --body:#333333;
  --muted:#f0f0f2;
  --line:#d8d9de;
  --white:#ffffff;
}
*{margin:0;padding:0;box-sizing:border-box}
html,body{width:1200px;height:3612px;overflow:hidden;background:var(--white)}
body{position:relative;font-family:"Open Sans",Arial,sans-serif;color:var(--body)}
.abs{position:absolute}
.btn{position:absolute;background:var(--orange);color:var(--white);font-family:"Tinos","Times New Roman",serif;font-weight:700;text-transform:uppercase;display:flex;align-items:center;justify-content:center;border-radius:20px;letter-spacing:.3px}

/* header + hero */
.hero{position:absolute;left:0;top:0;width:1200px;height:691px;background:radial-gradient(circle at 370px 340px,#3a2a1e 0,#16203a 22%,#081630 45%,#071226 70%),linear-gradient(90deg,#0a1428,#0d2040 70%,#102a52);}
.hero-glow{position:absolute;left:190px;top:130px;width:360px;height:410px;border-radius:50%;background:radial-gradient(circle,rgba(235,150,70,.35),rgba(40,70,140,.15) 55%,transparent 70%)}
.brand{position:absolute;display:flex;align-items:center;gap:12px;color:var(--white);font-family:"Montserrat",sans-serif;font-weight:600}
.brand-mark{width:36px;height:36px;border:3px solid var(--white);border-radius:50%}
.top-nav{position:absolute;top:33px;left:557px;display:flex;gap:37px;font-family:"Montserrat",sans-serif;font-weight:700;font-size:13px;color:var(--white)}
.hero-title{position:absolute;left:652px;top:226px;font-family:"Montserrat",sans-serif;font-weight:900;font-size:48px;line-height:58px;color:var(--white)}
.hero-text{position:absolute;left:653px;top:364px;width:400px;font-size:18px;line-height:30px;color:#e6e8ee}
.dots{position:absolute;left:562px;top:642px;display:flex;gap:11px}
.dots span{width:7px;height:7px;border-radius:50%;background:var(--white)}
.dots span.on{background:var(--orange)}

/* section title */
.sec-title{position:absolute;left:0;width:1200px;text-align:center;font-family:"Montserrat",sans-serif;font-weight:700;font-size:22px;color:var(--ink)}
.rule{position:absolute;left:562px;top:791px;width:76px;height:2px;background:var(--ink)}

/* features */
.feature{position:absolute;width:300px;text-align:center}
.feature-art{width:182px;height:178px;margin:0 auto;border-radius:50%;background:radial-gradient(circle,#f3ebe0 0,#eee3d4 60%,#fff 72%)}
.feature h3{margin-top:49px;font-family:"Montserrat",sans-serif;font-weight:700;font-size:16.5px;color:var(--ink)}
.feature p{margin-top:12px;font-size:13px;line-height:19.5px;color:#333}

/* courses */
.courses{position:absolute;left:0;top:1189px;width:1200px;height:631px;background:linear-gradient(180deg,var(--navy) 0,var(--navy) 55%,#0c2650 80%,#123a72 100%)}
.courses .sec-title{color:var(--white)}
.courses-sub{position:absolute;top:95px;left:0;width:1200px;text-align:center;font-size:13px;line-height:22px;color:#d9dde6}
.card{position:absolute;top:183px;width:295px;height:387px;background:var(--white);border-radius:6px}
.card-art{position:absolute;left:11px;top:15px;width:272px;height:176px;border-radius:4px}
.card h4{position:absolute;left:22px;top:214px;width:250px;font-family:"Montserrat",sans-serif;font-weight:700;font-size:14.5px;line-height:21px;color:var(--ink)}
.card p{position:absolute;left:22px;top:262px;width:230px;font-size:12px;line-height:18px;color:#333}
.card .btn{left:22px;top:329px;width:111px;height:35px;font-size:12px}

/* certified */
.cert-art{position:absolute;left:140px;top:1879px;width:463px;height:420px;border-radius:48% 52% 46% 54%/55% 50% 50% 45%;background:radial-gradient(circle at 50% 50%,#f4f6fb 0,#e7ecf7 55%,#d3ddf3 100%)}
.big-head{position:absolute;font-family:"Montserrat",sans-serif;font-weight:800;color:var(--ink);text-transform:uppercase}
.lead{position:absolute;font-size:16px;line-height:25.5px;color:#333}

/* turnkey */
.turnkey{position:absolute;left:0;top:2362px;width:1200px;height:588px;background:var(--muted)}
.grid-v{position:absolute;left:809px;top:2425px;width:1px;height:460px;background:var(--line)}
.grid-h{position:absolute;left:544px;top:2657px;width:526px;height:1px;background:var(--line)}
.service{position:absolute;width:262px;text-align:center}
.service-icon{width:92px;height:92px;margin:0 auto;border-radius:50%;background:var(--navy);display:flex;align-items:center;justify-content:center}
.service h3{margin-top:18px;font-family:"Montserrat",sans-serif;font-weight:700;font-size:16px;color:var(--ink)}
.service p{margin-top:9px;font-size:12.5px;line-height:19px;color:#333}

/* experts */
.experts{position:absolute;left:0;top:2950px;width:1200px;height:466px;background:linear-gradient(90deg,#eef0f0 0,#eceeed 45%,#d9dbd8 60%,#3a3b3e 78%,#6d6a66 100%)}
.experts-photo{position:absolute;left:620px;top:0;width:580px;height:466px;background:linear-gradient(160deg,rgba(30,30,34,.0) 0,rgba(25,25,30,.85) 40%,rgba(150,110,70,.7) 85%,#c08a56 100%)}

/* footer */
.footer{position:absolute;left:0;top:3416px;width:1200px;height:196px;background:var(--footer);color:var(--white)}
.foot-nav{position:absolute;left:477px;top:54px;display:flex;gap:37px;font-family:"Montserrat",sans-serif;font-weight:500;font-size:13px}
.foot-rule{position:absolute;left:135px;top:108px;width:935px;height:1px;background:#2a3a5c}
.follow{position:absolute;left:138px;top:146px;display:flex;align-items:center;gap:22px;font-family:"Montserrat",sans-serif;font-size:11.5px}
.social{width:14px;height:14px;border-radius:50%;background:var(--white)}
.copyright{position:absolute;right:136px;top:146px;font-family:"Montserrat",sans-serif;font-size:11.5px}
</style>
</head>
<body>

<header class="hero" role="img" aria-label="Dark blue background photo of a glowing digital coin with streams of code">
  <div class="hero-glow"></div>
</header>
<div class="brand" style="left:31px;top:23px;font-size:29px"><span class="brand-mark"></span>Vimbral</div>
<nav class="top-nav"><span>HOME</span><span>ABOUT US</span><span>COURSES</span><span>CERTIFICATIONS</span><span>NEWS</span><span>CONTACT US</span></nav>
<h1 class="hero-title">Build Your<br>Better Future</h1>
<p class="hero-text">Lorem Ipsum is simply dummy text of the printing and typesetting industry.</p>
<a class="btn" style="left:652px;top:463px;width:144px;height:49px;font-size:17px;border-radius:24px">Read More</a>
<div class="dots"><span></span><span></span><span class="on"></span><span></span><span></span></div>

<h2 class="sec-title" style="top:743px">LAND YOUR DREAM JOB WITH VIMBRAL</h2>
<div class="rule"></div>

<div class="feature" style="left:90px;top:838px">
  <div class="feature-art" role="img" aria-label="Illustration of a person writing on a large checklist"></div>
  <h3>Learn Unique Skills</h3>
  <p>Lorem Ipsum is simply dummy text<br>of the printing and typesettin.</p>
</div>
<div class="feature" style="left:450px;top:838px">
  <div class="feature-art" role="img" aria-label="Illustration of a graduation cap with a diploma and gear"></div>
  <h3>Get Blockchain Certified</h3>
  <p>Lorem Ipsum is simply dummy text<br>of the printing and typesettin.</p>
</div>
<div class="feature" style="left:811px;top:838px">
  <div class="feature-art" role="img" aria-label="Illustration of a person climbing rising blocks toward a graduation cap"></div>
  <h3>Work with Passion</h3>
  <p>Lorem Ipsum is simply dummy text<br>of the printing and typesettin.</p>
</div>

<section class="courses" role="img" aria-label="Dark navy band with a faint glowing network pattern along the bottom">
  <h2 class="sec-title" style="top:48px">EXPLORE OUR COURSES</h2>
  <p class="courses-sub">Lorem Ipsum is simply dummy text&nbsp; of the printing and typesettin passages<br>of Lorem Ipsum available, but the majority have</p>
  <article class="card" style="left:133px">
    <div class="card-art" role="img" aria-label="Photo of a digital coin with binary code" style="background:radial-gradient(circle at 45% 40%,#b88a52 0,#3d4f78 45%,#16264a 100%)"></div>
    <h4>Lorem Ipsum is simply dumm text of the printing</h4>
    <p>Contrary to popular belief, Lorem Ipsum is not simply random text. It has roots in a piece of classical</p>
    <a class="btn">Get Started</a>
  </article>
  <article class="card" style="left:453px">
    <div class="card-art" role="img" aria-label="Isometric illustration of a payment card connected to digital nodes" style="background:linear-gradient(135deg,#2f6ff0,#3a82ff 55%,#2a5ee0)"></div>
    <h4>Lorem Ipsum is simply dumm text of the printing</h4>
    <p>Contrary to popular belief, Lorem Ipsum is not simply random text. It has roots in a piece of classical</p>
    <a class="btn">Get Started</a>
  </article>
  <article class="card" style="left:775px">
    <div class="card-art" role="img" aria-label="Illustration of people working around a large dashboard screen" style="background:linear-gradient(135deg,#2a2d35,#34373f 60%,#262930)"></div>
    <h4>Lorem Ipsum is simply dumm text of the printing</h4>
    <p>Contrary to popular belief, Lorem Ipsum is not simply random text. It has roots in a piece of classical</p>
    <a class="btn">Get Started</a>
  </article>
</section>

<div class="cert-art" role="img" aria-label="Illustration of two people reviewing a certified checklist on a laptop"></div>
<h2 class="big-head" style="left:677px;top:1914px;font-size:39px;line-height:46.5px">Become<br>Blockchain<br>Certified</h2>
<p class="lead" style="left:678px;top:2076px;width:380px">There are many variations of passages of Lorem Ipsum available, but the majority have suffered alteration in some form, by injected.</p>
<a class="btn" style="left:679px;top:2183px;width:119px;height:40px;font-size:16px">Join Now</a>

<section class="turnkey"></section>
<h2 class="big-head" style="left:135px;top:2494px;font-size:30.5px;line-height:40px">Turnkey Course<br>Creation with<br>Vimbral</h2>
<p class="lead" style="left:136px;top:2638px;width:300px">There are many variations of passages of Lorem Ipsum available, but the majority have suffered alteration in some form, by injected.</p>
<a class="btn" style="left:135px;top:2772px;width:119px;height:39px;font-size:16px">Join Now</a>

<div class="grid-v"></div>
<div class="grid-h"></div>

<div class="service" style="left:518px;top:2426px">
  <div class="service-icon"><svg width="46" height="46" viewBox="0 0 46 46" fill="none" stroke="#fff" stroke-width="2"><rect x="9" y="5" width="28" height="24" rx="2"/><path d="M14 12h18M14 17h18M14 22h10"/><path d="M11 36l12-6 12 6-12 6z"/></svg></div>
  <h3>Educational Content</h3>
  <p>Lorem Ipsum is simply dummy text<br>of the printing and typesettin.</p>
</div>
<div class="service" style="left:823px;top:2426px">
  <div class="service-icon"><svg width="46" height="46" viewBox="0 0 46 46" fill="none" stroke="#fff" stroke-width="2.2"><circle cx="23" cy="23" r="17"/><path d="M23 6v34M6 23h34"/><circle cx="23" cy="14" r="3"/><circle cx="32" cy="23" r="3"/></svg></div>
  <h3>Easy Integration</h3>
  <p>Lorem Ipsum is simply dummy text<br>of the printing and typesettin.</p>
</div>
<div class="service" style="left:518px;top:2695px">
  <div class="service-icon"><svg width="46" height="46" viewBox="0 0 46 46" fill="none" stroke="#fff" stroke-width="2"><rect x="11" y="7" width="24" height="33" rx="2"/><rect x="17" y="4" width="12" height="6" rx="1"/><rect x="15" y="15" width="5" height="5"/><rect x="15" y="24" width="5" height="5"/><rect x="15" y="33" width="5" height="4"/><path d="M23 17h8M23 26h8M23 35h8"/></svg></div>
  <h3>Learning Assessments</h3>
  <p>Lorem Ipsum is simply dummy text<br>of the printing and typesettin.</p>
</div>
<div class="service" style="left:823px;top:2695px">
  <div class="service-icon"><svg width="48" height="48" viewBox="0 0 48 48" fill="none" stroke="#fff" stroke-width="2"><path d="M24 6l9 5v10l-9 5-9-5V11z"/><path d="M15 21l9 5 9-5"/><path d="M14 24l9 5v10l-9 5-9-5V29z"/><path d="M34 24l9 5v10l-9 5-9-5V29z"/></svg></div>
  <h3>Faculty Training</h3>
  <p>Lorem Ipsum is simply dummy text<br>of the printing and typesettin.</p>
</div>

<section class="experts"><div class="experts-photo" role="img" aria-label="Photo of hands typing on a laptop on a wooden desk beside a glass terrarium"></div></section>
<h2 class="big-head" style="left:130px;top:3022px;font-size:30.5px;line-height:41px">Learn from<br>Industry Experts</h2>
<p class="lead" style="left:133px;top:3122px;width:320px;font-size:13.5px;line-height:21px">There are many variations of passages of Lorem Ipsum available, but the majority have suffered alteration in some form, by injected.</p>
<a class="btn" style="left:133px;top:3216px;width:133px;height:38px;font-size:16px">Read More</a>

<footer class="footer">
  <div class="brand" style="left:135px;top:44px;font-size:28px"><span class="brand-mark"></span>Vimbral</div>
  <nav class="foot-nav"><span>HOME</span><span>ABOUT US</span><span>COURSES</span><span>CERTIFICATIONS</span><span>NEWS</span><span>CONTACT US</span></nav>
  <div class="foot-rule"></div>
  <div class="follow"><span>FOLLOW US</span><span class="social"></span><span class="social"></span><span class="social"></span></div>
  <div class="copyright">Copyright © 2021 All Rights Reserved</div>
</footer>

</body>
</html>
```